Statement on the current financial and economic crisis, with a focus on Greece,

Anybody can become angry - that is easy, but to be angry with the right person and to the right degree and at the right time and for the right purpose, and in the right way - that is not within everybody's power and is not easy.
(Pherondes ) greek philosopher

i want to do a poster with this words from Pherondes greek philosopher and to show this statement for the greek people... its about for my project that i am doing.

Target Market(s)

my audience will be greek people but not only, from 18-80 years old for that reason i want my statement to be in english.

Industry/Entity Type

Financial

Requirements
Must have
• Anybody can become angry - that is easy, but to be angry with the right person and to the right degree and at the right time and for the right purpose, and in the right way - that is not within everybody's power and is not easy.
i want to show in my poster this statement from:
Pherondes greek philosopher (384 – 322 BC)

```html
<!DOCTYPE html>
<html lang="en">
<head>
<meta charset="utf-8">
<title>Anybody Can Become Angry — Poster</title>
<link rel="stylesheet" href="https://fonts.googleapis.com/css2?family=Marcellus+SC&display=swap">
<style>
  :root {
    --paper: #ffffff;
    --ink: #111111;
    --de-black: #111111;
    --de-red: #d90000;
    --de-gold: #ffcc00;
    --se-blue: #1e8ee6;
    --se-yellow: #ffee00;
    --hu-red: #cc0000;
    --hu-white: #ffffff;
    --hu-green: #44dd22;
    --uk-blue: #1a1aa6;
    --uk-red: #cc0000;
    --es-red: #cc1111;
    --es-yellow: #ffee11;
    --fr-blue: #1c3cf0;
    --fr-red: #ff1a00;
    --gr-blue: #4a9be8;
    --gr-white: #ffffff;
    --sleeve: #111111;
    --skin: #fcd4a4;
  }
  * { margin: 0; padding: 0; box-sizing: border-box; }
  html, body { width: 907px; height: 1200px; overflow: hidden; background: var(--paper); }
  .poster { position: relative; width: 907px; height: 1200px; background: var(--paper); overflow: hidden; }
  .flags { position: absolute; inset: 0 0 auto 0; width: 907px; height: 340px; }
  .greek-flag-in-hand {
    position: absolute; left: 0; top: 215px; width: 855px; height: 740px;
    background: linear-gradient(160deg, var(--gr-blue) 0%, #9cc8f2 45%, var(--gr-blue) 70%, #f5d6b4 88%, var(--sleeve) 100%);
    clip-path: polygon(14% 0, 100% 8%, 100% 44%, 62% 72%, 18% 60%, 0 78%, 0 100%, 0 28%, 10% 14%);
  }
  .quote {
    position: absolute; left: 120px; top: 762px; width: 780px;
    text-align: center; font-family: "Marcellus SC", serif; color: var(--ink);
  }
  .quote__lead { font-size: 66px; line-height: 56px; letter-spacing: 1px; }
  .quote__body { margin-top: 22px; font-size: 25px; line-height: 41px; letter-spacing: 0.5px; }
  .quote__source { margin-top: 10px; font-size: 19px; letter-spacing: 1.5px; }
</style>
</head>
<body>
<main class="poster">
  <svg class="flags" viewBox="0 0 907 340" aria-hidden="true">
    <!-- Germany -->
    <g class="flag flag--germany">
      <rect x="0" y="0" width="238" height="40" fill="var(--de-black)"/>
      <rect x="0" y="40" width="238" height="46" fill="var(--de-red)"/>
      <rect x="0" y="86" width="238" height="50" fill="var(--de-gold)"/>
    </g>
    <!-- Sweden -->
    <g class="flag flag--sweden">
      <rect x="238" y="0" width="362" height="92" fill="var(--se-blue)"/>
      <rect x="238" y="0" width="362" height="24" fill="var(--se-yellow)"/>
      <rect x="322" y="0" width="38" height="92" fill="var(--se-yellow)"/>
    </g>
    <!-- Hungary -->
    <g class="flag flag--hungary">
      <rect x="600" y="0" width="307" height="40" fill="var(--hu-red)"/>
      <rect x="600" y="40" width="307" height="60" fill="var(--hu-white)"/>
      <rect x="600" y="100" width="307" height="28" fill="var(--hu-green)"/>
    </g>
    <!-- United Kingdom -->
    <g class="flag flag--uk">
      <rect x="0" y="136" width="284" height="150" fill="var(--uk-blue)"/>
      <path d="M0 136 L284 286 M284 136 L0 286" stroke="#fff" stroke-width="30"/>
      <path d="M0 136 L284 286 M284 136 L0 286" stroke="var(--uk-red)" stroke-width="10"/>
      <rect x="0" y="189" width="284" height="44" fill="#fff"/>
      <rect x="117" y="136" width="50" height="150" fill="#fff"/>
      <rect x="0" y="198" width="284" height="26" fill="var(--uk-red)"/>
      <rect x="128" y="136" width="28" height="150" fill="var(--uk-red)"/>
    </g>
    <!-- Spain -->
    <g class="flag flag--spain">
      <rect x="278" y="70" width="326" height="48" fill="var(--es-red)"/>
      <rect x="278" y="118" width="326" height="108" fill="var(--es-yellow)"/>
      <rect x="278" y="226" width="326" height="40" fill="var(--es-red)"/>
    </g>
    <!-- France -->
    <g class="flag flag--france">
      <rect x="604" y="127" width="96" height="203" fill="var(--fr-blue)"/>
      <rect x="700" y="127" width="108" height="203" fill="#fff"/>
      <rect x="808" y="127" width="99" height="203" fill="var(--fr-red)"/>
    </g>
  </svg>

  <div class="greek-flag-in-hand" role="img" aria-label="Illustration of a suited arm and hand holding a waving blue and white Greek flag"></div>

  <section class="quote">
    <p class="quote__lead">"Anybody can<br>become angry ~</p>
    <p class="quote__body">
      That is easy, but to be angry with<br>
      the right person and to the right degree<br>
      and at the right time<br>
      and for the right purpose, and in the right way-<br>
      that is not within everybody’s power<br>
      and is not easy."
    </p>
    <p class="quote__source">Pherondes Greek philosopher (384-322BC)</p>
  </section>
</main>
</body>
</html>
```